4th Generation Family Business Needs a New Card Design!

We are a family owned 4th Generation company. We are based in the Sydney, Australia area and we are desperately in need of a more modern and classy card. We are monumental masons who design, supply & erect lasting memorials throughout cemeteries in Sydney. Our customers are normally in a period of grieving. I have attached logo files that will need to be implemented on the card. Company was established 1935. Australian Owned and Operated. Card needs to be designed to PIXO.com specification.

Target Market(s)

Our target market is based upon people that a grieving for family members that have passed away. We also deal with alot of companies that own and operate cemeteries.

Industry/Entity Type

Business

Contact Information for Business Card

Simon Harcourt, Operations Manager, 0417293086, simon@harcourtmemorials.com.au
Lewis Harcourt, Director, 0491630572, lewis@harcourtmemorials.com.au
Phone # 02 9561 3048
Website: www.harcourtmemorials.com.au
Address: Suite 17, 8 Palfrey Lane, West Carlow, Sydney NSW 2156

Font styles to use
Serif
Decorative
Script

Requirements
Must have
• Would like to see the logo nicely implemented with a modern design. Embossed lettering would be a nice additive.

```html
<!DOCTYPE html>
<html lang="en">
<head>
<meta charset="utf-8">
<title>Harcourt Memorials – Business Card</title>
<link href="https://fonts.googleapis.com/css2?family=Cinzel:wght@400;700&family=Open+Sans:wght@400&display=swap" rel="stylesheet">
<style>
  :root {
    --backdrop: #d9d9d9;
    --card-white: #ffffff;
    --card-soft: #efefef;
    --ink: #1f1c1d;
    --charcoal: #221f20;
    --gold: #f0bf1c;
    --light: #ffffff;
  }
  * { box-sizing: border-box; margin: 0; padding: 0; }
  html, body { width: 1200px; height: 900px; overflow: hidden; }
  body {
    background: var(--backdrop);
    position: relative;
    font-family: "Open Sans", Arial, sans-serif;
    color: var(--ink);
  }
  .card {
    position: absolute;
    width: 560px;
    height: 320px;
    box-shadow: 0 6px 18px rgba(0,0,0,0.18);
    overflow: hidden;
  }
  /* Front card */
  .card-front {
    left: 560px; top: 90px;
    background: var(--card-white);
    display: flex; flex-direction: column; align-items: center; justify-content: center;
    text-align: center;
  }
  .brand-name {
    font-family: "Cinzel", Georgia, serif;
    font-weight: 700;
    font-size: 38px;
    line-height: 1.1;
    letter-spacing: 1px;
    color: var(--ink);
  }
  .brand-name span { display: block; }
  .front-address {
    margin-top: 22px;
    font-size: 15px;
    line-height: 1.4;
  }
  /* Back card */
  .card-back {
    left: 120px; top: 480px;
    background: var(--card-soft);
  }
  .back-shape { position: absolute; inset: 0; }
  .back-brand {
    position: absolute;
    left: 16px; top: 122px; width: 215px;
    text-align: center;
  }
  .back-brand .brand-name { color: var(--light); font-size: 27px; }
  .contacts {
    position: absolute;
    right: 24px; top: 28px;
    text-align: right;
    font-size: 13px;
    line-height: 1.35;
  }
  .person { margin-bottom: 12px; }
  .person-name {
    font-family: "Cinzel", Georgia, serif;
    font-weight: 700;
    font-size: 17px;
  }
  .person-role {
    font-family: "Cinzel", Georgia, serif;
    font-size: 13px;
    letter-spacing: 0.5px;
  }
  .line { display: flex; justify-content: flex-end; align-items: center; gap: 6px; }
  .icon { width: 11px; height: 11px; flex: none; fill: var(--ink); }
  .company-lines { margin-top: 4px; }
</style>
</head>
<body>

  <section class="card card-front" aria-label="Business card front">
    <div class="brand-name"><span>Harcourt</span><span>Memorials</span></div>
    <p class="front-address">Suite 17, 8 Palfrey Lane, West Carlow,<br>Sydney NSW 2156</p>
  </section>

  <section class="card card-back" aria-label="Business card back">
    <svg class="back-shape" viewBox="0 0 560 320" width="560" height="320" aria-hidden="true">
      <path d="M0 0 H230 C290 80 270 230 150 320 H0 Z" fill="var(--charcoal)"/>
      <path d="M246 0 C308 80 288 232 168 320 H154 C274 232 294 80 234 0 Z" fill="var(--gold)"/>
    </svg>

    <div class="back-brand">
      <div class="brand-name"><span>Harcourt</span><span>Memorials</span></div>
    </div>

    <div class="contacts">
      <div class="person">
        <div class="person-name">Simon Harcourt</div>
        <div class="person-role">Operations Manager</div>
        <div class="line">0417293086
          <svg class="icon" viewBox="0 0 12 12"><path d="M3 0h6v12H3zM4 1.5v8h4v-8z"/></svg></div>
        <div class="line">simon@harcourtmemorials.com.au
          <svg class="icon" viewBox="0 0 12 12"><path d="M0 2h12v8H0z"/></svg></div>
      </div>
      <div class="person">
        <div class="person-name">Lewis Harcourt</div>
        <div class="person-role">Director</div>
        <div class="line">0491630572
          <svg class="icon" viewBox="0 0 12 12"><path d="M3 0h6v12H3zM4 1.5v8h4v-8z"/></svg></div>
        <div class="line">lewis@harcourtmemorials.com.au
          <svg class="icon" viewBox="0 0 12 12"><path d="M0 2h12v8H0z"/></svg></div>
      </div>
      <div class="company-lines">
        <div class="line">02 9561 3048
          <svg class="icon" viewBox="0 0 12 12"><path d="M1 3c0-1 1-2 5-2s5 1 5 2v1H8V3H4v1H1zM3 5h6l2 6H1z"/></svg></div>
        <div class="line">www.harcourtmemorials.com.au
          <svg class="icon" viewBox="0 0 12 12"><circle cx="6" cy="6" r="5.5"/></svg></div>
      </div>
    </div>
  </section>

</body>
</html>
```